PSD Designs needed to give to my Developer

Hello, I need PSD files to give to my programmer for the creation of my new website. The website is for KORVA lane, a new clothing company based in Chicago, IL. We sell womens, mens and kids fashion. We specialize in jackets, outerwear and sweaters, but we sell clothing from every category, I have someone working on the logo, so I can't include it for reference. However, I have included 2 reference sites as well as a PDF of how the 2 reference sites could be merged together. The main company color should be blue (hence the name KORVA lane), and the overall feel of the site should be FUN. It should communicate: This is where you want to shop if you want a FUN, HAPPY experience. I need the Home Page file designed very quickly. Whoever is awarded this job will immediately continue working with me to design the other 8 pages. I will pay for all pages. The amount I am offering is for this one page only, and I will pay you additional to design all other 8 pages. Thank you for your time and I will be picking the best design so that we can immediately build a great relationship and work through the rest of the project.

Industry/Entity Type

Apparel Store

Number of Pages Required

1 page

Font styles to use
Sans Serif

Colors
33a6d7
0492cd
ffffff

Requirements
Must have
• I have included all notes in the project description so please check there. My project must communicate: Fun and Happy Design. Even tho I have chosen a few variations of blue below, I still want the designer to incorporate other colors as necessary to acheive the desired look.
Should not have
• It should have a boring, childish feel

```html
<!DOCTYPE html>
<html lang="en">
<head>
<meta charset="utf-8">
<title>KORVA lane — Home</title>
<link href="https://fonts.googleapis.com/css2?family=Open+Sans:wght@400;600;700&family=Montserrat:wght@600;700&display=swap" rel="stylesheet">
<style>
  :root{
    --blue:#0492cd;
    --blue-light:#33a6d7;
    --hero-bg:#c9dff0;
    --white:#ffffff;
    --ink:#222222;
    --muted:#777777;
    --topbar:#1f1f1f;
    --soft:#f3f3f3;
    --line:#dddddd;
  }
  *{box-sizing:border-box;margin:0;padding:0}
  html,body{width:678px;height:1200px;overflow:hidden;background:var(--white)}
  body{font-family:"Open Sans",Arial,sans-serif;color:var(--ink);position:relative}

  .topbar{height:14px;background:var(--topbar);color:var(--white);font-size:6px;display:flex;align-items:center;justify-content:space-between;padding:0 14px}
  .topbar b{color:var(--blue-light)}

  .site-header{height:48px;display:flex;align-items:center;justify-content:space-between;padding:0 86px 0 88px}
  .main-nav{display:flex;gap:18px;font-size:6.5px;font-weight:600;letter-spacing:.3px}
  .main-nav a{color:var(--ink);text-decoration:none;padding-bottom:3px}
  .main-nav a.active{color:var(--blue);border-bottom:2px solid var(--blue)}
  .brand{display:flex;align-items:center;gap:6px;font-family:"Open Sans",Arial,sans-serif;font-weight:600;font-size:14px;color:var(--ink);letter-spacing:.5px}
  .brand-dot{width:9px;height:9px;border-radius:50%;background:var(--blue-light)}

  .hero{position:absolute;left:0;top:62px;width:678px;height:198px;background:var(--hero-bg)}
  .hero-inner{position:absolute;left:82px;top:0;width:516px;height:198px}
  .hero-photo{position:absolute;left:18px;top:0;width:180px;height:193px;background:linear-gradient(160deg,#d6e4ee,#a98461 60%,#6f5a48)}
  .hero-copy{position:absolute;left:256px;top:58px;width:250px}
  .hero-copy h1{font-family:"Montserrat",Arial,sans-serif;font-size:15px;font-weight:700;margin-bottom:14px;white-space:nowrap}
  .hero-copy p{font-size:6px;line-height:9px;color:#444;margin-bottom:12px}
  .btn{display:inline-block;border:1.5px solid var(--ink);font-size:6px;font-weight:700;padding:5px 12px;letter-spacing:.5px;color:var(--ink);background:transparent}
  .btn.light{border-color:var(--white);color:var(--white);background:rgba(255,255,255,.1)}
  .btn.solid{background:var(--white);border-color:var(--white)}

  .promo{position:absolute;overflow:hidden}
  .promo .label{position:absolute;font-family:"Montserrat",Arial,sans-serif;font-weight:700;font-size:14px}
  .promo .btn{position:absolute}
  .promo-shop{left:82px;top:264px;width:252px;height:124px;background:linear-gradient(120deg,#b9c6cf,#6c7b87 55%,#3c4650)}
  .promo-retail{left:346px;top:264px;width:252px;height:124px;background:linear-gradient(120deg,#d8d2c7,#c8b446 55%,#2ea3a8)}
  .promo-happier{left:82px;top:396px;width:516px;height:180px;background:linear-gradient(100deg,#8d6c56,#b58372 35%,#5d7b8e 70%,#a3473e)}
  .tag{position:absolute;left:0;top:20px;width:70px;height:30px;background:rgba(255,255,255,.9)}

  .products{position:absolute;left:0;top:606px;width:678px;text-align:center}
  .products h2{font-family:"Montserrat",Arial,sans-serif;font-size:17px;font-weight:700;margin-bottom:22px}
  .product-grid{display:flex;justify-content:center;gap:16px}
  .product-card{width:116px;height:154px}
  .p1{background:linear-gradient(160deg,#e8e8e8,#e5c62f 60%,#2aa0a0)}
  .p2{background:linear-gradient(160deg,#ececec,#a98461 60%,#4b4b50)}
  .p3{background:linear-gradient(160deg,#d7dde3,#3d7ab5 55%,#2b4e83)}
  .p4{background:linear-gradient(160deg,#e2e2e2,#8c9aa4 55%,#3b3f45)}

  .news-band{position:absolute;left:0;top:852px;width:678px;height:128px;background:linear-gradient(90deg,#4e4646,#7f6a6a 50%,#5b4f55)}
  .news-col{position:absolute;top:22px;width:246px;color:var(--white)}
  .news-col h3{font-size:9px;font-weight:700;margin-bottom:6px}
  .news-col p{font-size:5.5px;line-height:8px}
  .news-col .date{font-size:5.5px;font-weight:700;margin-top:6px}
  .news-left{left:88px}
  .news-right{left:346px}

  .info{position:absolute;left:0;top:980px;width:678px;height:172px;background:var(--soft)}
  .info-col{position:absolute;top:20px;width:240px;font-size:5.5px;line-height:8px;color:var(--muted)}
  .info-col p{margin-bottom:6px}
  .info-left{left:88px}
  .info-right{left:346px}

  .site-footer{position:absolute;left:0;top:1152px;width:678px;height:48px;border-top:1px solid var(--line)}
  .footer-nav{position:absolute;left:88px;top:10px;display:flex;gap:14px;font-size:5.5px;font-weight:600}
  .footer-nav span+span::before{content:"|";margin-right:14px;color:var(--muted)}
  .social{position:absolute;right:86px;top:8px;display:flex;gap:3px}
  .social span{width:10px;height:10px;display:block}
  .copyright{position:absolute;left:88px;top:26px;font-size:5px;color:var(--muted)}
</style>
</head>
<body>
  <div class="topbar">
    <span>Sign up now and get our newsletter <b>FREE GIFT</b></span>
    <span>Wishlist &nbsp; Login</span>
  </div>

  <header class="site-header">
    <nav class="main-nav">
      <a class="active">HOME</a><a>GIFTS FOR HER</a><a>WHAT NEW</a><a>NEW &amp; ON SALE</a><a>BRANDS &amp; STYLES</a>
    </nav>
    <div class="brand"><span class="brand-dot"></span>KORVA lane</div>
  </header>

  <section class="hero">
    <div class="hero-inner">
      <div class="hero-photo" role="img" aria-label="Smiling older man with glasses wearing a tan bomber jacket"></div>
      <div class="hero-copy">
        <h1>Older Man Bomber Jacket</h1>
        <p>Warm, light and ready for city weekends. Our classic bomber is cut for comfort with soft lining, ribbed cuffs and a relaxed fit you will love.</p>
        <span class="btn">SHOP NOW</span>
      </div>
    </div>
  </section>

  <div class="promo promo-shop" role="img" aria-label="Young man in cap and sunglasses with shopping bags">
    <span class="tag"></span>
    <span class="label" style="left:6px;top:27px;color:var(--ink)">Shop</span>
    <span class="btn solid" style="left:10px;top:66px">SHOP NOW</span>
  </div>
  <div class="promo promo-retail" role="img" aria-label="Cheerful woman in a teal beanie and yellow sweater">
    <span class="tag"></span>
    <span class="label" style="left:6px;top:22px;color:var(--ink);font-size:11px;line-height:12px">Retail<br>Therapy</span>
    <span class="btn solid" style="left:10px;top:66px">SHOP NOW</span>
  </div>
  <div class="promo promo-happier" role="img" aria-label="Group of happy friends shopping together with colourful bags">
    <span class="label" style="left:224px;top:64px;color:var(--white)">Be Happier</span>
    <span class="btn light" style="left:232px;top:92px">SHOP NOW</span>
  </div>

  <section class="products">
    <h2>Our Products</h2>
    <div class="product-grid">
      <div class="product-card p1" role="img" aria-label="Woman in teal beanie and yellow knit sweater"></div>
      <div class="product-card p2" role="img" aria-label="Man in tan bomber jacket"></div>
      <div class="product-card p3" role="img" aria-label="Child in blue winter hat and jacket"></div>
      <div class="product-card p4" role="img" aria-label="Young man in cap with backpack"></div>
    </div>
  </section>

  <section class="news-band" role="img" aria-label="Blurred shopping street background">
    <div class="news-col news-left">
      <h3>News</h3>
      <p>Our new winter collection has arrived in store and online. Discover cozy knits, bright parkas and fun accessories for the whole family this season.</p>
      <p class="date">3 March 2019</p>
    </div>
    <div class="news-col news-right">
      <h3>Informationen</h3>
      <p>Free shipping on all orders over fifty dollars. Easy returns within thirty days, friendly help from our team and gift wrapping for every special occasion.</p>
    </div>
  </section>

  <section class="info">
    <div class="info-col info-left">
      <p>KORVA lane is a fashion store for women, men and kids. We love jackets, outerwear and sweaters, and we carry clothing from every category so the whole family can find something new and bright.</p>
      <p>Our team picks every piece with care, mixing comfort with colour. Visit our store to try on the latest arrivals and enjoy a happy shopping day with friends.</p>
    </div>
    <div class="info-col info-right">
      <p>Sign up for our newsletter to get early news on sales, new brands and seasonal styles, plus a free gift with your first order.</p>
      <p>Questions about sizes, orders or delivery? Our helpful staff is ready to answer by chat or email every day of the week.</p>
      <p>Follow us for outfit ideas, style tips and fun events.</p>
    </div>
  </section>

  <footer class="site-footer">
    <div class="footer-nav"><span>HOME</span><span>GIFTS FOR HER</span><span>ABOUT</span><span>FAQ &amp; HELP</span><span>INFORMATIONEN</span></div>
    <div class="social">
      <span style="background:#3b5998"></span><span style="background:#1da1f2"></span><span style="background:#dd4b39"></span><span style="background:#cb2027"></span><span style="background:#0077b5"></span><span style="background:#e4405f"></span>
    </div>
    <div class="copyright">© 2019 KORVA lane. All rights reserved.</div>
  </footer>
</body>
</html>
```